Business Card Design Project

We need a Business Card for an Mechanical Engineering firm in Singapore. The design should be Modern & Technical looking, yet eye catching.

Our company deals in Cutting Tools & Machine Accessories for the Manufacturing Industries such as Oil & Gas, Aero Space, etc... For more information on our Company, you can either email me or view our website www.torvalen.com.sg.

We are trying to revamp our image to give our consumers a fresh new perspective to our company, so we welcome all ideas.

Industry/Entity Type

Business

Requirements
Must have
• Must incorporate New Company Logo into the card as shown in Uploaded file.

```html
<!DOCTYPE html>
<html lang="en">
<head>
<meta charset="utf-8">
<title>Torvalen Tools – Business Card</title>
<link rel="stylesheet" href="https://fonts.googleapis.com/css2?family=Open+Sans:wght@400;600;700&display=swap">
<style>
  :root {
    --backdrop: #d9d9d9;
    --card: #ffffff;
    --brand-red: #8e1b22;
    --panel-red: #a3232b;
    --band-dark: #1c1414;
    --ink: #222222;
    --muted: #f2e4e4;
  }
  * { box-sizing: border-box; margin: 0; padding: 0; }
  html, body { width: 1200px; height: 951px; overflow: hidden; }
  body {
    background: var(--backdrop);
    font-family: "Open Sans", Arial, sans-serif;
    color: var(--ink);
    position: relative;
  }
  .card {
    position: absolute;
    background: var(--card);
    border-radius: 22px;
    overflow: hidden;
    box-shadow: 0 6px 18px rgba(0,0,0,.18);
  }
  .card--front { left: 90px; top: 90px; width: 560px; height: 320px; }
  .card--back  { left: 500px; top: 520px; width: 620px; height: 354px; }

  .brand {
    display: flex; align-items: center; gap: 12px;
    font-weight: 700; color: var(--brand-red);
    letter-spacing: 1px; text-transform: uppercase;
  }
  .brand__dot { border-radius: 50%; background: var(--brand-red); flex: none; }

  .card--front .brand { position: absolute; left: 0; right: 0; top: 110px; justify-content: center; font-size: 38px; }
  .card--front .brand__dot { width: 22px; height: 22px; }
  .card--front .website {
    position: absolute; left: 0; right: 0; top: 238px;
    text-align: center; font-size: 19px; letter-spacing: .5px;
  }

  .back__panel { position: absolute; inset: 0; }
  .card--back .brand { position: absolute; left: 34px; top: 42px; font-size: 27px; }
  .card--back .brand__dot { width: 16px; height: 16px; }

  .contact { position: absolute; left: 34px; top: 124px; list-style: none; font-size: 15.5px; line-height: 1.3; }
  .contact li { display: flex; align-items: flex-start; gap: 8px; }
  .contact .group { margin-bottom: 14px; }
  .contact svg { width: 13px; height: 13px; margin-top: 3px; flex: none; fill: var(--brand-red); }

  .person { position: absolute; right: 40px; bottom: 30px; color: #fff; text-align: left; }
  .person__name { font-size: 22px; font-weight: 400; }
  .person__role { font-size: 15px; color: var(--muted); margin-left: 70px; }
</style>
</head>
<body>

<section class="card card--front">
  <div class="brand"><span class="brand__dot"></span>Torvalen Tools</div>
  <p class="website">www.torvalentools.com</p>
</section>

<section class="card card--back">
  <svg class="back__panel" viewBox="0 0 620 354" preserveAspectRatio="none" aria-hidden="true">
    <path d="M385 0 C300 130 270 260 300 354 L332 354 C305 260 330 120 405 0 Z" fill="var(--band-dark)"/>
    <path d="M405 0 C330 120 305 260 332 354 L620 354 L620 0 Z" fill="var(--panel-red)"/>
  </svg>

  <div class="brand"><span class="brand__dot"></span>Torvalen Tools</div>

  <ul class="contact">
    <li class="group">
      <svg viewBox="0 0 12 12"><path d="M6 1 L11.5 6 H10 V11 H7.5 V8 H4.5 V11 H2 V6 H.5 Z"/></svg>
      <span>4150 Kell Arbor Rd.<br>Marlow, TX 78119</span>
    </li>
    <li>
      <svg viewBox="0 0 12 12"><path d="M3 1 L5 3.5 L4 5 C5 7 6 8 7 8.5 L8.5 7.5 L11 9.5 L9.5 11 C5 11 1 7 1 2.5 Z"/></svg>
      <span>555-014-2270</span>
    </li>
    <li>
      <svg viewBox="0 0 12 12"><rect x="3" y="0.5" width="6" height="11" rx="1.2"/><rect x="4" y="2" width="4" height="6.5" fill="#fff"/></svg>
      <span>555-014-2271</span>
    </li>
    <li>
      <svg viewBox="0 0 12 12"><rect x="0.5" y="2.5" width="11" height="7.5" rx="1"/><path d="M1 3 L6 7 L11 3" stroke="#fff" stroke-width="1" fill="none"/></svg>
      <span>info@torvalentools.com</span>
    </li>
    <li>
      <svg viewBox="0 0 12 12"><circle cx="6" cy="6" r="5.5"/></svg>
      <span>www.torvalentools.com</span>
    </li>
  </ul>

  <div class="person">
    <p class="person__name">Alan Verhoek</p>
    <p class="person__role">director</p>
  </div>
</section>

</body>
</html>
```